Finiding oppertunites in Real Estate 6.15.20

size of ad 7” x 9.6”
1-I like the ad to stand out and attract people's attention.
2-you should be able to see the text of the ad clearly .. see the attachment anything in yellow is instructions.
3-the list of topics should not be the main part of the ad
4-if you decide you want a picture or vector of a person .. (you decide)
then it should be a white male about 25-30 years old wearing a solid white or blue shirt and not long hair.
5-leave 1 inch for footer
see attachment
Good luck

Target Market(s)

potential male students 25-35 years of age

Industry/Entity Type

Education

Requirements
Must have
• will stand out and people would want to see it.
should be able to read the words of ad
Nice to have
• how to make money in real estate on one line

```html
<!DOCTYPE html>
<html lang="en">
<head>
<meta charset="utf-8">
<title>Real Estate Career Course Flyer</title>
<link href="https://fonts.googleapis.com/css2?family=League+Spartan:wght@700;800&family=Josefin+Sans:wght@300;400;600;700&display=swap" rel="stylesheet">
<style>
  :root {
    --stage: #5a5a5a;
    --paper: #f3f3f3;
    --navy: #1f3a68;
    --band-top: #2c3658;
    --band-bottom: #161d35;
    --gold: #c3a872;
    --gold-deep: #a8864a;
    --beige: #d8ccb2;
    --ink: #222222;
    --ink-soft: #3b3b3b;
    --white: #ffffff;
  }
  * { box-sizing: border-box; margin: 0; padding: 0; }
  html, body { width: 1200px; height: 1200px; overflow: hidden; background: var(--stage); }
  .flyer {
    position: absolute; left: 182px; top: 10px; width: 835px; height: 1180px;
    background: linear-gradient(to bottom, var(--paper) 0%, var(--paper) 66%, #e6dfcf 80%, var(--beige) 100%);
    font-family: "Josefin Sans", sans-serif; color: var(--ink); overflow: hidden;
  }
  .title {
    position: absolute; left: 0; top: 50px; width: 100%; text-align: center;
    font-family: "League Spartan", sans-serif; font-weight: 800; color: var(--navy);
    font-size: 62px; line-height: 54px; letter-spacing: 1px;
  }
  .tagline {
    position: absolute; background: var(--gold); color: var(--ink);
    font-size: 22px; height: 40px; line-height: 44px; text-align: center; white-space: nowrap;
  }
  .tagline--question { left: 211px; top: 184px; width: 412px; }
  .tagline--audience { left: 58px; top: 236px; width: 718px; }
  .tagline--promise { left: 73px; top: 287px; width: 687px; }
  .houses-photo {
    position: absolute; left: 0; top: 356px; width: 100%; height: 162px;
    background: radial-gradient(ellipse at 46% 70%, #c93a36 0 3%, transparent 4%),
                linear-gradient(to bottom, #eeeeee, #d4d4d4 55%, #f0f0f0);
  }
  .course-band {
    position: absolute; left: 40px; top: 542px; width: 755px; height: 262px;
    background: linear-gradient(to bottom, var(--band-top), var(--band-bottom));
  }
  .remote-illustration {
    position: absolute; left: 28px; top: 34px; width: 275px; height: 100px;
    background: linear-gradient(90deg, #9ab3cf 0 22%, transparent 22%),
                linear-gradient(to bottom, #e8893a, #d8641f);
    border-radius: 4px;
  }
  .remote-label {
    position: absolute; left: 28px; top: 130px; font-family: "League Spartan", sans-serif;
    font-weight: 800; font-size: 60px; line-height: 56px; color: var(--gold);
  }
  .sessions-label {
    position: absolute; left: 28px; top: 178px; font-weight: 300; font-size: 62px;
    line-height: 60px; color: var(--white); letter-spacing: 1px;
  }
  .band-divider { position: absolute; left: 376px; top: 22px; width: 3px; height: 222px; background: var(--gold); }
  .session-count {
    position: absolute; left: 414px; top: 52px; font-family: "League Spartan", sans-serif;
    font-weight: 800; font-size: 104px; line-height: 90px; color: var(--gold);
  }
  .session-word {
    position: absolute; left: 523px; top: 48px; font-family: "League Spartan", sans-serif;
    font-weight: 800; font-size: 54px; line-height: 40px; color: var(--white);
  }
  .start-date {
    position: absolute; left: 405px; top: 138px; width: 330px; text-align: center;
    font-weight: 300; font-size: 40px; line-height: 43px; color: var(--white);
  }
  .topics-heading {
    position: absolute; left: 0; top: 840px; width: 100%; text-align: center;
    font-weight: 700; font-size: 28px; color: var(--ink-soft);
  }
  .topics-list { position: absolute; top: 886px; list-style: none; }
  .topics-list li {
    display: flex; align-items: center; gap: 12px; height: 31px;
    font-size: 15px; color: var(--ink-soft);
  }
  .topics-list svg { width: 17px; height: 17px; flex: none; }
  .topics-list--one { left: 105px; }
  .topics-list--two { left: 346px; }
  .topics-list--three { left: 588px; }
  .footer { position: absolute; left: 0; top: 1060px; width: 100%; height: 120px; background: var(--paper); }
  .company { position: absolute; left: 38px; top: 36px; font-size: 15px; line-height: 19px; }
  .company-name { color: var(--gold-deep); }
  .contacts { position: absolute; left: 280px; top: 36px; list-style: none; font-size: 15px; }
  .contacts li { display: flex; align-items: center; gap: 10px; height: 21px; }
  .contacts svg { width: 14px; height: 14px; }
  .hotline { position: absolute; right: 42px; top: 40px; text-align: right; font-weight: 800; }
  .hotline-label { font-family: "League Spartan", sans-serif; color: var(--gold-deep); font-size: 24px; line-height: 22px; }
  .hotline-number { font-family: "Josefin Sans", sans-serif; font-weight: 700; font-style: italic; font-size: 24px; line-height: 26px; }
</style>
</head>
<body>
<main class="flyer">
  <h1 class="title">REAL ESTATE<br>CAREER COURSE</h1>
  <p class="tagline tagline--question">How to Make Money In Real Estate?</p>
  <p class="tagline tagline--audience">For those who have started or would like to go into Real Estate.</p>
  <p class="tagline tagline--promise">An investment in knowledge opens up untold opportunities.</p>

  <div class="houses-photo" role="img" aria-label="Photo of rows of small white model houses with one red house in front"></div>

  <section class="course-band">
    <div class="remote-illustration" role="img" aria-label="Illustration of a man on a laptop watching an online real estate lesson"></div>
    <p class="remote-label">REMOTE</p>
    <p class="sessions-label">SESSIONS</p>
    <div class="band-divider"></div>
    <p class="session-count">12</p>
    <p class="session-word">session<br>course</p>
    <p class="start-date">Classes starting<br>June 16</p>
  </section>

  <h2 class="topics-heading">A partial listing of Topics</h2>
  <ul class="topics-list topics-list--one">
    <li><svg viewBox="0 0 17 17"><rect x="1" y="3" width="13" height="13" fill="none" stroke="#c3a872" stroke-width="1.3"/><path d="M4 9l3 3 8-9" fill="none" stroke="#c3a872" stroke-width="1.4"/></svg>Single-family</li>
    <li><svg viewBox="0 0 17 17"><rect x="1" y="3" width="13" height="13" fill="none" stroke="#c3a872" stroke-width="1.3"/><path d="M4 9l3 3 8-9" fill="none" stroke="#c3a872" stroke-width="1.4"/></svg>Multifamily</li>
    <li><svg viewBox="0 0 17 17"><rect x="1" y="3" width="13" height="13" fill="none" stroke="#c3a872" stroke-width="1.3"/><path d="M4 9l3 3 8-9" fill="none" stroke="#c3a872" stroke-width="1.4"/></svg>Management</li>
    <li><svg viewBox="0 0 17 17"><rect x="1" y="3" width="13" height="13" fill="none" stroke="#c3a872" stroke-width="1.3"/><path d="M4 9l3 3 8-9" fill="none" stroke="#c3a872" stroke-width="1.4"/></svg>Real Estate Concepts</li>
    <li><svg viewBox="0 0 17 17"><rect x="1" y="3" width="13" height="13" fill="none" stroke="#c3a872" stroke-width="1.3"/><path d="M4 9l3 3 8-9" fill="none" stroke="#c3a872" stroke-width="1.4"/></svg>Real Estate law</li>
  </ul>
  <ul class="topics-list topics-list--two">
    <li><svg viewBox="0 0 17 17"><rect x="1" y="3" width="13" height="13" fill="none" stroke="#c3a872" stroke-width="1.3"/><path d="M4 9l3 3 8-9" fill="none" stroke="#c3a872" stroke-width="1.4"/></svg>Investment properties</li>
    <li><svg viewBox="0 0 17 17"><rect x="1" y="3" width="13" height="13" fill="none" stroke="#c3a872" stroke-width="1.3"/><path d="M4 9l3 3 8-9" fill="none" stroke="#c3a872" stroke-width="1.4"/></svg>Foreclosures</li>
    <li><svg viewBox="0 0 17 17"><rect x="1" y="3" width="13" height="13" fill="none" stroke="#c3a872" stroke-width="1.3"/><path d="M4 9l3 3 8-9" fill="none" stroke="#c3a872" stroke-width="1.4"/></svg>Rehab</li>
    <li><svg viewBox="0 0 17 17"><rect x="1" y="3" width="13" height="13" fill="none" stroke="#c3a872" stroke-width="1.3"/><path d="M4 9l3 3 8-9" fill="none" stroke="#c3a872" stroke-width="1.4"/></svg>Foreclosures</li>
    <li><svg viewBox="0 0 17 17"><rect x="1" y="3" width="13" height="13" fill="none" stroke="#c3a872" stroke-width="1.3"/><path d="M4 9l3 3 8-9" fill="none" stroke="#c3a872" stroke-width="1.4"/></svg>Short sales</li>
  </ul>
  <ul class="topics-list topics-list--three">
    <li><svg viewBox="0 0 17 17"><rect x="1" y="3" width="13" height="13" fill="none" stroke="#c3a872" stroke-width="1.3"/><path d="M4 9l3 3 8-9" fill="none" stroke="#c3a872" stroke-width="1.4"/></svg>Development</li>
    <li><svg viewBox="0 0 17 17"><rect x="1" y="3" width="13" height="13" fill="none" stroke="#c3a872" stroke-width="1.3"/><path d="M4 9l3 3 8-9" fill="none" stroke="#c3a872" stroke-width="1.4"/></svg>Finical modeling</li>
    <li><svg viewBox="0 0 17 17"><rect x="1" y="3" width="13" height="13" fill="none" stroke="#c3a872" stroke-width="1.3"/><path d="M4 9l3 3 8-9" fill="none" stroke="#c3a872" stroke-width="1.4"/></svg>HUD properties</li>
    <li><svg viewBox="0 0 17 17"><rect x="1" y="3" width="13" height="13" fill="none" stroke="#c3a872" stroke-width="1.3"/><path d="M4 9l3 3 8-9" fill="none" stroke="#c3a872" stroke-width="1.4"/></svg>Due Diligence e</li>
  </ul>

  <footer class="footer">
    <div class="company">
      <p class="company-name">Company Name</p>
      <p>Address Line 01</p>
      <p>Address Line 02</p>
    </div>
    <ul class="contacts">
      <li><svg viewBox="0 0 14 14"><path d="M1 5c0-2 2-3 6-3s6 1 6 3l-3 1-1-2H5L4 6 1 5zM3 7h8l1 5H2z" fill="#a8864a"/></svg>+000 1234 5678</li>
      <li><svg viewBox="0 0 14 14"><rect x="1" y="3" width="12" height="9" fill="#a8864a"/><path d="M1 3l6 5 6-5" fill="none" stroke="#f3f3f3" stroke-width="1.2"/></svg>hello@emailaddress.com</li>
      <li><svg viewBox="0 0 14 14"><rect x="1" y="2" width="12" height="8" fill="none" stroke="#a8864a" stroke-width="1.4"/><path d="M5 12h4" stroke="#a8864a" stroke-width="1.4"/></svg>www.website.com</li>
    </ul>
    <div class="hotline">
      <p class="hotline-label">HOTLINE</p>
      <p class="hotline-number">012345678911</p>
    </div>
  </footer>
</main>
</body>
</html>
```